Brintel Works - Fast, Efficient and Gas Mainteance for Domestic, Commercial and Industrial clients

We are in the process of purchasing a new business and would like to get a new logo and business card.
Business is a gas maintenance business that also does new gas installations.
Has been established since 1988.
Services include:
Install all types of gas appliances & equipment inc. hot water units
Maintain / repair / replace all types of gas appliances & equipment

Target Market(s)

Domestic, Commercial and Industrial clients

Industry/Entity Type

Business

Contact Information for Business Card

admin@brintelworks.com.au
07 3918 4726
Brintel Works PTY LTD

Logo Text

Gas Fitting & Plumbing Maintenance Specialists

Font styles to use
Sans Serif

Requirements
Must have
• Logo
• Business name, contact number, email address, web address
• Domestic | Commercial | Industrial Est Since 1988
Nice to have
• Possibly a black card with a flame logo to one side
Should not have
• Spelling errors

```html
<!DOCTYPE html>
<html lang="en">
<head>
<meta charset="utf-8">
<title>Brintel Works – Business Card</title>
<link href="https://fonts.googleapis.com/css2?family=Questrial&display=swap" rel="stylesheet">
<style>
  :root {
    --backdrop: #e9e6e3;
    --card-black: #000000;
    --brand-red: #ec2227;
    --brand-orange: #f47920;
    --brand-yellow: #ffd400;
    --text-white: #ffffff;
    --flame-deep: #7a2a05;
    --flame-mid: #e0780f;
    --flame-light: #ffc23a;
  }
  * { margin: 0; padding: 0; box-sizing: border-box; }
  html, body { width: 1200px; height: 900px; overflow: hidden; }
  body {
    background: var(--backdrop);
    font-family: "Questrial", "Century Gothic", sans-serif;
    position: relative;
  }
  .card {
    position: absolute;
    background: var(--card-black);
    overflow: hidden;
    box-shadow: 0 6px 18px rgba(0,0,0,0.25);
  }

  /* Front card */
  .card--front { left: 77px; top: 34px; width: 588px; height: 364px; }
  .front-bands { position: absolute; inset: 0; }
  .brand-dot {
    position: absolute; left: 170px; top: 92px;
    width: 44px; height: 44px; border-radius: 50%;
    background: var(--brand-red);
  }
  .wordmark { position: absolute; color: var(--brand-yellow); font-weight: 400; }
  .card--front .wordmark-name {
    left: 230px; top: 72px; font-size: 58px; line-height: 1;
  }
  .card--front .wordmark-sub {
    left: 238px; top: 136px; font-size: 16px; letter-spacing: 2.4px; line-height: 1;
  }
  .contact-list {
    position: absolute; right: 310px; top: 254px;
    list-style: none; color: var(--text-white); font-size: 15px;
  }
  .contact-list li {
    display: flex; align-items: center; justify-content: flex-end;
    height: 25px; gap: 10px;
  }
  .contact-list svg { width: 12px; height: 12px; flex: none; margin-right: -22px; }
  .contact-list .contact-text { margin-right: 0; }
  .address {
    position: absolute; left: 341px; top: 265px;
    color: var(--text-white); font-size: 15px; line-height: 24px; font-style: normal;
  }

  /* Back card */
  .card--back { left: 388px; top: 505px; width: 567px; height: 352px; }
  .card--back .wordmark-name {
    left: 32px; top: 30px; font-size: 74px; line-height: 1;
  }
  .card--back .wordmark-sub {
    left: 43px; top: 108px; font-size: 20px; letter-spacing: 3px; line-height: 1;
  }
  .flame-area {
    position: absolute; left: 170px; top: 118px; width: 397px; height: 234px;
    background:
      radial-gradient(ellipse 70% 60% at 55% 85%, var(--flame-light) 0%, var(--flame-mid) 45%, rgba(122,42,5,0.6) 75%, transparent 100%);
  }
</style>
</head>
<body>

  <section class="card card--front" aria-label="Business card front">
    <svg class="front-bands" width="588" height="364" viewBox="0 0 588 364" aria-hidden="true">
      <polygon points="0,229 383,229 412,191 588,191 588,364 0,364" fill="var(--brand-red)"/>
      <polygon points="0,198 406,198 380,226 0,226" fill="var(--brand-orange)"/>
      <polyline points="0,227 381,227 409,193" fill="none" stroke="#000" stroke-width="2"/>
    </svg>

    <span class="brand-dot" aria-hidden="true"></span>
    <div class="wordmark wordmark-name">Brintel</div>
    <div class="wordmark wordmark-sub">WORKS PTY LTD</div>

    <ul class="contact-list">
      <li><span class="contact-text">07 3918 4726</span>
        <svg viewBox="0 0 24 24" aria-hidden="true"><path fill="#fff" d="M6.6 10.8a15.1 15.1 0 0 0 6.6 6.6l2.2-2.2a1 1 0 0 1 1-.25 11.4 11.4 0 0 0 3.6.57 1 1 0 0 1 1 1V20a1 1 0 0 1-1 1A17 17 0 0 1 3 4a1 1 0 0 1 1-1h3.5a1 1 0 0 1 1 1c0 1.25.2 2.45.57 3.57a1 1 0 0 1-.25 1z"/></svg>
      </li>
      <li><span class="contact-text">admin@brintelworks.com.au</span>
        <svg viewBox="0 0 24 24" aria-hidden="true"><path fill="#fff" d="M2 5h20v14H2z"/><path fill="none" stroke="var(--brand-red)" stroke-width="2" d="M2 6l10 7 10-7"/></svg>
      </li>
      <li><span class="contact-text">www.brintelworks.com.au</span>
        <svg viewBox="0 0 24 24" aria-hidden="true"><g fill="none" stroke="#fff" stroke-width="2.5"><rect x="2" y="10" width="10" height="6" rx="3" transform="rotate(-45 7 13)"/><rect x="12" y="8" width="10" height="6" rx="3" transform="rotate(-45 17 11)"/></g></svg>
      </li>
    </ul>

    <address class="address">12345, Address Goes Here<br>Country Name, 123456</address>
  </section>

  <section class="card card--back" aria-label="Business card back">
    <div class="wordmark wordmark-name">Brintel</div>
    <div class="wordmark wordmark-sub">WORKS PTY LTD</div>
    <div class="flame-area" role="img" aria-label="Photograph of orange gas flames rising along the bottom edge"></div>
  </section>

</body>
</html>
```